Bath Salt Packaging

Hello! We are Dr Velmo Organics, a company providing the best and most nutritious food and health-care products for the health conscious around the world!
We are currently in the process of releasing a few new products, one of which is Himalayan Bath Salt Crystals. It is an ancient, pure salt which has been protected from environmental toxins and pollution under the Himalayan mountains for more than 250 million years!
Our salt is 100% pure and unrefined, still containing the original mineral composition of the ancient life-giving ocean that supported our early ancestors. There are over 60 trace minerals in this salt, the majority of which exist in colloidal forms, meaning they are highly bioavailable and quickly ionized when added to water.
So, we need packaging designed for our four salt packets; a 300mL jar, a 150mL jar, a 10g sachet and a box which will house the sachets. I have attached the label content, measurements and a little extra instruction/information.
We want a natural, eco-friendly feel for the packaging. Thanks!
ps. please use the 3rd of the Logo's (TM, 'Organics' under leaf)

```html
<!DOCTYPE html>
<html lang="en">
<head>
<meta charset="utf-8">
<title>Himalayan Bath Salt Crystals – Jar Label</title>
<link href="https://fonts.googleapis.com/css2?family=Oswald:wght@500&family=Yellowtail&family=Open+Sans:wght@400;700&display=swap" rel="stylesheet">
<style>
  :root {
    --page: #f4f3f1;
    --label: #ffffff;
    --forest: #1f4a37;
    --leaf: #5fa02a;
    --badge-green: #6dbb2f;
    --ink: #3a3a3a;
    --mist: #f3f2ee;
    --stone: #b7b19c;
    --earth: #8c8566;
  }
  html, body {
    margin: 0;
    padding: 0;
    width: 1200px;
    height: 961px;
    overflow: hidden;
    background: var(--page);
  }
  .canvas {
    position: relative;
    width: 1200px;
    height: 961px;
  }
  .label {
    position: absolute;
    left: 380px;
    top: 95px;
    width: 440px;
    height: 770px;
    background: var(--label);
    box-shadow: 0 2px 10px rgba(0,0,0,0.08);
    overflow: hidden;
  }
  .brand {
    position: absolute;
    top: 80px;
    left: 0;
    width: 100%;
    display: flex;
    justify-content: center;
    align-items: center;
    gap: 10px;
    font-family: "Oswald", sans-serif;
    font-weight: 500;
    font-size: 30px;
    color: var(--ink);
    letter-spacing: 0.5px;
  }
  .brand-dot {
    width: 14px;
    height: 14px;
    border-radius: 50%;
    background: var(--leaf);
  }
  .product-name {
    position: absolute;
    top: 215px;
    left: 0;
    width: 100%;
    text-align: center;
    font-family: "Yellowtail", cursive;
    font-size: 72px;
    line-height: 1;
    color: var(--forest);
  }
  .product-type {
    position: absolute;
    top: 304px;
    left: 0;
    width: 100%;
    text-align: center;
    font-family: "Oswald", sans-serif;
    font-weight: 500;
    font-size: 42px;
    line-height: 1;
    color: var(--leaf);
    letter-spacing: -0.5px;
  }
  .mountain-scene {
    position: absolute;
    left: 0;
    top: 360px;
    width: 100%;
    height: 410px;
    background:
      linear-gradient(180deg, var(--label) 0%, var(--mist) 18%, #d9d5c6 40%, var(--mist) 58%, var(--stone) 80%, var(--earth) 100%);
  }
  .badge {
    position: absolute;
    left: 222px;
    top: 470px;
    width: 200px;
    height: 200px;
  }
  .volume {
    position: absolute;
    top: 712px;
    left: 0;
    width: 100%;
    text-align: center;
    font-family: "Open Sans", sans-serif;
    font-size: 17px;
    color: var(--forest);
  }
  .volume strong { font-weight: 700; }
</style>
</head>
<body>
<main class="canvas">
  <section class="label">
    <div class="brand"><span class="brand-name">Dr Velmo Organics</span><span class="brand-dot"></span></div>
    <h1 class="product-name" style="margin:0;font-weight:400;">Himalayan</h1>
    <div class="product-type">BATH SALT CRYSTALS</div>
    <div class="mountain-scene" role="img" aria-label="Misty photograph of Himalayan mountain peaks in muted sepia tones"></div>
    <svg class="badge" viewBox="0 0 200 200" aria-hidden="true">
      <circle cx="100" cy="100" r="97" fill="var(--badge-green)"/>
      <circle cx="100" cy="100" r="90" fill="#ffffff"/>
      <circle cx="100" cy="100" r="84" fill="var(--badge-green)"/>
      <circle cx="100" cy="100" r="60" fill="#ffffff"/>
    </svg>
    <div class="badge-photo" role="img" aria-label="Portrait photograph of the company doctor in a white coat"
         style="position:absolute;left:272px;top:520px;width:100px;height:100px;border-radius:50%;background:linear-gradient(180deg,#e6e6e6 0%,#c9cdd2 60%,#eef0f2 100%);"></div>
    <div class="volume"><strong>300</strong>mL</div>
  </section>
</main>
</body>
</html>
```